Tree Service Billboard 20x8 ft

We need a billboard design for a tree service company.
The billboard is 20ft x 8 ft so we need a design that is capable to stretching to those dimensions without loosing quality.
I have attached a series of images.
Image 1- Simply a billboard that I think looks good that I would like you to use for inspiration. I am aiming for the same format only no color in the wording, just black white, or gray. I like the the trees in the background, the logo placed to the left, and wording on the right.
Image 2- Current Logo I would like to the left of the billboard
Image 3- Another format of current logo if needed.
Image 4- A drawn out design template
Image 5- Another drawn out design template

Specific things I am looking for
-The contact number to be the largest thing on the design
-The logo on the design
-Key points to the design to say:
Tree Removal
Tree Trimming
Land Development
Stump Grinding
Storm Response
Insured
Free Bids
-The leafbook logo
-The searchly Logo

```html
<!DOCTYPE html>
<html lang="en">
<head>
<meta charset="utf-8">
<title>Birchline Tree Service – Billboard 20x8</title>
<link rel="stylesheet" href="https://fonts.googleapis.com/css2?family=Montserrat:wght@600;800;900&display=swap">
<style>
  :root {
    --ink: #0d0d0d;
    --steel: #6b6b6b;
    --paper: #efefef;
    --stage-top: #a9a9a9;
    --stage-mid: #cfcfcf;
    --white: #ffffff;
  }
  * { box-sizing: border-box; margin: 0; padding: 0; }
  html, body { width: 928px; height: 1200px; overflow: hidden; }
  body {
    background: radial-gradient(ellipse at 50% 50%, var(--stage-mid) 0%, var(--stage-top) 85%);
    font-family: "Montserrat", Arial, sans-serif;
    position: relative;
  }
  .billboard {
    position: absolute;
    left: 44px; top: 432px;
    width: 840px; height: 336px;
    background: var(--paper);
    overflow: hidden;
    box-shadow: 0 18px 26px rgba(0,0,0,0.28);
  }
  .billboard__backdrop {
    position: absolute; inset: 0;
    background:
      linear-gradient(180deg, rgba(255,255,255,0.55) 0%, rgba(255,255,255,0.1) 45%, rgba(230,230,230,0.6) 100%),
      linear-gradient(90deg, #d4d4d4 0%, #ececec 30%, #e2e2e2 60%, #f0f0f0 100%);
  }
  .brand__ring {
    position: absolute;
    left: 164px; top: 26px;
    width: 168px; height: 168px;
    border: 6px solid var(--ink);
    border-radius: 50%;
  }
  .brand__name {
    position: absolute;
    left: 40px; top: 214px;
    width: 420px;
    text-align: center;
    white-space: nowrap;
    font-weight: 900;
    font-size: 25px;
    letter-spacing: -0.3px;
    color: var(--steel);
    text-transform: uppercase;
    line-height: 1;
  }
  .phone-band {
    position: absolute;
    left: 0; bottom: 0;
    width: 462px; height: 68px;
    background: var(--ink);
    clip-path: polygon(0 0, 435px 0, 100% 100%, 0 100%);
    display: flex; align-items: center;
    padding-left: 30px;
    gap: 8px;
  }
  .phone-band svg { width: 30px; height: 30px; flex: none; }
  .phone-band__number {
    font-weight: 900;
    font-size: 47px;
    letter-spacing: -0.5px;
    white-space: nowrap;
    background: linear-gradient(180deg, #ffffff 40%, #9a9a9a 100%);
    -webkit-background-clip: text; background-clip: text;
    color: transparent;
  }
  .base-rule {
    position: absolute; left: 440px; right: 0; bottom: 0;
    height: 7px; background: var(--ink);
  }
  .services {
    position: absolute;
    left: 0; top: 26px;
    width: 840px;
    list-style: none;
  }
  .service {
    position: absolute;
    height: 32px;
    color: var(--white);
    font-weight: 800;
    font-size: 21px;
    line-height: 32px;
    text-align: center;
    white-space: nowrap;
    text-transform: uppercase;
    clip-path: polygon(3% 0, 100% 0, 97% 100%, 0 100%);
  }
  .service--dark { background: var(--ink); }
  .service--grey { background: var(--steel); }
  .social {
    position: absolute;
    left: 700px; top: 256px;
    width: 128px;
    text-align: center;
    color: var(--ink);
  }
  .social__names {
    display: flex; justify-content: center; gap: 8px;
    font-weight: 800; font-size: 12px;
    margin-bottom: 4px;
  }
  .social__caption { font-weight: 800; font-size: 10px; line-height: 1.2; }
</style>
</head>
<body>
  <section class="billboard" aria-label="Birchline Tree Service billboard">
    <div class="billboard__backdrop" role="img" aria-label="Faded grey photo of a park with leafy trees and blossoms"></div>

    <div class="brand">
      <div class="brand__ring"></div>
      <h1 class="brand__name">Birchline Tree Service</h1>
    </div>

    <ul class="services">
      <li class="service service--dark" style="left:474px; top:0;   width:258px;">Tree Removal</li>
      <li class="service service--grey" style="left:472px; top:41px; width:262px;">Tree Trimming</li>
      <li class="service service--dark" style="left:435px; top:82px; width:336px;">Land Development</li>
      <li class="service service--grey" style="left:463px; top:123px; width:280px;">Stump Grinding</li>
      <li class="service service--dark" style="left:458px; top:164px; width:290px;">Storm Response</li>
      <li class="service service--grey" style="left:522px; top:205px; width:162px;">Insured</li>
      <li class="service service--dark" style="left:512px; top:246px; width:182px;">Free Bids</li>
    </ul>

    <div class="social">
      <div class="social__names"><span>leafbook</span><span>searchly</span></div>
      <p class="social__caption">Find us on leafbook<br>and searchly</p>
    </div>

    <div class="base-rule"></div>
    <div class="phone-band">
      <svg viewBox="0 0 24 24" aria-hidden="true">
        <path fill="#fff" d="M6.6 10.8a15.1 15.1 0 0 0 6.6 6.6l2.2-2.2c.3-.3.7-.4 1-.2 1.1.4 2.3.6 3.6.6.6 0 1 .4 1 1V20c0 .6-.4 1-1 1A17 17 0 0 1 3 4c0-.6.4-1 1-1h3.5c.6 0 1 .4 1 1 0 1.3.2 2.5.6 3.6.1.3 0 .7-.2 1z"/>
        <path fill="none" stroke="#fff" stroke-width="1.6" stroke-linecap="round" d="M14 3.5a7 7 0 0 1 6.5 6.5M14 7a3.5 3.5 0 0 1 3 3"/>
      </svg>
      <span class="phone-band__number">555-014-2286</span>
    </div>
  </section>
</body>
</html>
```